Lanternfield Drinks business cards

We need a business card design for our new logo. The company is modern, progressive, professional, yet approachable. The key products are ready to drink bottles and cans of coffee based beverages.
These cards will be a critical part of the first impression made by our sales organization, business development team, and all external facing personnel.
Card can be a vertical or horizontal orientation.

Target Market(s)

Customers, suppliers, business partners

Industry/Entity Type

Business

Contact Information for Business Card

Business cards should feature Company Name and Logo.

Font styles to use
Serif

Colors

Designer to choose colors to be used in the design.

Requirements
Must have
• Strong readability of Name, phone #, mobile number and email address.
• Job title, website url, Street Address, and other details can be secondary level readability.
Nice to have
• High impact, simplistic quality design.
• Ok to utilize the 'H in the box' separate from the company name

```html
<!DOCTYPE html>
<html lang="en">
<head>
<meta charset="UTF-8">
<title>Lanternfield Drinks – Business Card</title>
<link rel="stylesheet" href="https://fonts.googleapis.com/css2?family=Cinzel:wght@700&family=Montserrat:wght@400;500&display=swap">
<style>
  :root {
    --stage: #161616;
    --card-dark-top: #2b2628;
    --card-dark-bottom: #1b191a;
    --orange: #e8662a;
    --orange-deep: #e4572b;
    --amber: #f4a93a;
    --gold: #e3a22c;
    --white: #ffffff;
    --text-light: #e9e6e6;
    --strip: #ececec;
  }
  * { box-sizing: border-box; margin: 0; padding: 0; }
  html, body { width: 1200px; height: 864px; overflow: hidden; }
  body {
    background: var(--stage);
    position: relative;
    font-family: "Montserrat", Arial, sans-serif;
  }
  .card {
    position: absolute;
    top: 278px;
    width: 540px;
    height: 308px;
    overflow: hidden;
    box-shadow: 0 10px 30px rgba(0,0,0,.6);
  }

  /* Front */
  .card-front {
    left: 40px;
    background: linear-gradient(160deg, var(--card-dark-top), var(--card-dark-bottom));
  }
  .brand {
    position: absolute;
    left: 34px; top: 30px;
    display: flex; align-items: center; gap: 10px;
  }
  .brand-square {
    width: 30px; height: 30px;
    background: var(--orange);
  }
  .brand-name {
    font-family: "Cinzel", Georgia, serif;
    font-weight: 700;
    font-size: 21px;
    color: var(--orange);
    letter-spacing: .5px;
  }
  .person {
    position: absolute;
    left: 34px; top: 96px;
    padding-left: 14px;
    border-left: 4px solid var(--gold);
  }
  .person-name {
    font-family: "Cinzel", Georgia, serif;
    font-weight: 700;
    font-size: 15px;
    color: var(--orange);
    letter-spacing: .4px;
  }
  .person-title {
    font-size: 11.5px;
    color: var(--text-light);
    margin-top: 1px;
  }
  .contact-list {
    position: absolute;
    left: 44px; top: 150px;
    list-style: none;
  }
  .contact-item {
    display: flex; align-items: center; gap: 12px;
    font-size: 11.5px;
    color: var(--text-light);
    height: 21px;
  }
  .contact-icon { width: 14px; height: 14px; flex: none; }
  .bottom-band {
    position: absolute;
    left: 0; right: 0; bottom: 0;
    height: 54px;
    background: linear-gradient(90deg, var(--orange-deep), var(--amber) 60%, var(--gold));
  }
  .bottom-band::before {
    content: "";
    position: absolute; left: 0; right: 0; top: 14px; height: 8px;
    background: rgba(255,255,255,.18);
  }
  .bottom-band::after {
    content: "";
    position: absolute; left: 0; right: 0; top: 32px; height: 5px;
    background: rgba(255,255,255,.12);
  }

  /* Back */
  .card-back {
    left: 620px;
    background: linear-gradient(150deg, var(--amber), var(--orange) 55%, var(--orange-deep));
  }
  .back-strip {
    position: absolute;
    left: 0; right: 0; bottom: 0;
    height: 70px;
    background: var(--strip);
    clip-path: polygon(0 0, 100% 100%, 0 100%);
  }
  .back-brand {
    position: absolute;
    right: 40px; top: 50%;
    transform: translateY(-50%);
    display: flex; align-items: center; gap: 14px;
  }
  .back-square {
    width: 56px; height: 56px;
    background: var(--white);
  }
  .back-name {
    font-family: "Cinzel", Georgia, serif;
    font-weight: 700;
    font-size: 26px;
    color: var(--white);
    letter-spacing: .6px;
  }
</style>
</head>
<body>

  <section class="card card-front" aria-label="Business card front">
    <div class="brand">
      <span class="brand-square"></span>
      <span class="brand-name">LANTERNFIELD DRINKS</span>
    </div>

    <div class="person">
      <p class="person-name">DANIEL ARBERY</p>
      <p class="person-title">Managing Director</p>
    </div>

    <ul class="contact-list">
      <li class="contact-item">
        <svg class="contact-icon" viewBox="0 0 14 14" aria-hidden="true"><rect x="0.5" y="0.5" width="13" height="13" fill="none" stroke="#e3a22c"/><path d="M4 3.5l1.5 0 .8 2-1 .8a5 5 0 0 0 2.4 2.4l.8-1 2 .8v1.5c-4 .3-6.8-2.5-6.5-6.5z" fill="#e3a22c"/></svg>
        <span>425.555.0148</span>
      </li>
      <li class="contact-item">
        <svg class="contact-icon" viewBox="0 0 14 14" aria-hidden="true"><rect x="0.5" y="0.5" width="13" height="13" fill="none" stroke="#e3a22c"/><rect x="4.5" y="2.5" width="5" height="9" rx="1" fill="none" stroke="#e3a22c"/><circle cx="7" cy="10" r=".7" fill="#e3a22c"/></svg>
        <span>206.555.0172</span>
      </li>
      <li class="contact-item">
        <svg class="contact-icon" viewBox="0 0 14 14" aria-hidden="true"><rect x="0.5" y="0.5" width="13" height="13" fill="none" stroke="#e3a22c"/><rect x="3" y="4" width="8" height="6" fill="none" stroke="#e3a22c"/><path d="M3 4l4 3.2L11 4" fill="none" stroke="#e3a22c"/></svg>
        <span>dan@lanternfielddrinks.com</span>
      </li>
      <li class="contact-item">
        <svg class="contact-icon" viewBox="0 0 14 14" aria-hidden="true"><rect x="0.5" y="0.5" width="13" height="13" fill="none" stroke="#e3a22c"/><circle cx="7" cy="7" r="4" fill="none" stroke="#e3a22c"/><path d="M3 7h8M7 3c-2 2.5-2 5.5 0 8M7 3c2 2.5 2 5.5 0 8" fill="none" stroke="#e3a22c" stroke-width=".8"/></svg>
        <span>www.lanternfielddrinks.com</span>
      </li>
    </ul>

    <div class="bottom-band"></div>
  </section>

  <section class="card card-back" aria-label="Business card back">
    <div class="back-strip"></div>
    <div class="back-brand">
      <span class="back-square"></span>
      <span class="back-name">LANTERNFIELD DRINKS</span>
    </div>
  </section>

</body>
</html>
```